Technology, Futuristic Innovation & Artificial Intelligence

I am looking for something with Artificial Intelligence DNA strands....
Blue, black, with white dna strands........I like clean, crisp, professional and not busy look.................................................................................................................................................................................................................................................................................................................................................................................. Thanks!

Target Market(s)

Engineers and United States Government Contractors

Industry/Entity Type

Engineering

Contact Information for Business Card

I've uploaded my logo the certification logo.

Font styles to use
Serif

Colors
3176b5
33a6d7
ffffff

Requirements
Must have
• Name
• Title
• Address
• Phone number
• website name
• certification logo
Nice to have
• Something with Artificial Intelligence DNA strands......
• **Please note it would be nice to have the business card 3D or textured with raised images. Thanks
Should not have
• Please no feminine flowery designs....this is an engineering firm

```html
<!DOCTYPE html>
<html lang="en">
<head>
<meta charset="utf-8">
<title>Velmora Business Card</title>
<link rel="stylesheet" href="https://fonts.googleapis.com/css2?family=Work+Sans:wght@400;500&family=Roboto+Condensed:wght@400;700&display=swap">
<style>
  :root {
    --page: #e7e4df;
    --space-deep: #05070f;
    --space-mid: #101a44;
    --space-blue: #2a2f86;
    --band: #1d1e1f;
    --white: #ffffff;
    --silver: #d9dbe0;
    --accent: #3176b5;
    --accent-light: #33a6d7;
  }
  * { margin: 0; padding: 0; box-sizing: border-box; }
  html, body { width: 1200px; height: 930px; overflow: hidden; background: var(--page); }
  .canvas { position: relative; width: 1200px; height: 930px; }

  .card {
    position: absolute;
    left: 278px;
    width: 644px;
    height: 368px;
    border-radius: 22px;
    overflow: hidden;
    background: linear-gradient(100deg, var(--space-deep) 0%, var(--space-mid) 45%, var(--space-blue) 100%);
    box-shadow: 0 6px 18px rgba(0,0,0,0.25);
  }
  .card--front { top: 76px; }
  .card--back { top: 486px; }

  .card__backdrop {
    position: absolute; inset: 0;
    background:
      radial-gradient(ellipse at 30% 20%, rgba(51,166,215,0.28), transparent 55%),
      radial-gradient(ellipse at 70% 75%, rgba(49,118,181,0.30), transparent 60%);
  }
  .card__edge-line {
    position: absolute; left: 0; height: 2px;
    background: linear-gradient(90deg, var(--silver), rgba(217,219,224,0.2));
  }

  /* front */
  .info-band {
    position: absolute; left: 0; right: 0; top: 94px; height: 179px;
    background: var(--band);
  }
  .brand {
    position: absolute; display: flex; align-items: center; gap: 12px;
    font-family: "Work Sans", sans-serif; font-weight: 500; color: var(--white);
    letter-spacing: 0.06em; white-space: nowrap;
  }
  .brand__square { background: var(--accent-light); flex: none; }
  .brand--small { left: 56px; top: 60px; font-size: 34px; }
  .brand--small .brand__square { width: 24px; height: 24px; }
  .tagline {
    position: absolute; font-family: "Roboto Condensed", sans-serif; font-weight: 700;
    color: var(--white); letter-spacing: 0.01em; display: flex; align-items: center; gap: 6px;
    white-space: nowrap;
  }
  .tagline__rule { height: 2px; background: var(--white); }
  .tagline--small { left: 46px; top: 112px; font-size: 11px; }
  .tagline--small .tagline__rule { width: 108px; }

  .divider { position: absolute; left: 332px; top: 16px; width: 2px; height: 150px; background: var(--white); }

  .contact {
    position: absolute; left: 363px; top: 10px;
    font-family: "Work Sans", sans-serif; color: var(--white);
  }
  .contact__name { font-size: 25px; font-weight: 500; letter-spacing: 0.03em; line-height: 1.1; }
  .contact__title { font-size: 16px; margin-top: 2px; }
  .contact__address { font-size: 16px; line-height: 20px; margin-top: 10px; }
  .contact__list { list-style: none; margin-top: 6px; font-size: 16px; line-height: 20.5px; }
  .contact__list li { display: flex; align-items: center; gap: 9px; }
  .contact__icon { width: 10px; height: 10px; flex: none; }

  .naics {
    position: absolute; left: 0; right: 0; top: 294px; text-align: center;
    font-family: "Roboto Condensed", sans-serif; font-size: 23px; line-height: 29px;
    color: var(--white);
  }

  /* back */
  .brand--large { left: 50%; top: 140px; transform: translateX(-50%); font-size: 62px; gap: 18px; }
  .brand--large .brand__square { width: 44px; height: 44px; }
  .tagline--large { left: 134px; top: 222px; font-size: 15px; }
  .tagline--large .tagline__rule { width: 170px; }
  .badge { position: absolute; left: 302px; top: 268px; }
</style>
</head>
<body>
<main class="canvas">

  <section class="card card--front">
    <div class="card__backdrop" role="img" aria-label="Glowing blue circuit board traces on a starry deep-space background"></div>
    <div class="card__edge-line" style="top:45px;width:150px;"></div>
    <div class="card__edge-line" style="top:361px;left:45px;width:120px;"></div>

    <div class="info-band">
      <div class="brand brand--small"><span class="brand__square"></span>VELMORA</div>
      <div class="tagline tagline--small"><span class="tagline__rule"></span>BUILDING BETTER FUTURES</div>
      <div class="divider"></div>
      <div class="contact">
        <h1 class="contact__name">DANA WHITFIELD</h1>
        <p class="contact__title">CEO</p>
        <p class="contact__address">2180 Larkspur Road<br>Ridgeway, SC 29130</p>
        <ul class="contact__list">
          <li><svg class="contact__icon" viewBox="0 0 10 10"><path d="M2 0.5 L3.5 0.5 L4 3 L3 3.8 Q4 6.2 6.2 7 L7 6 L9.5 6.5 L9.5 8 Q9.5 9.5 8 9.5 Q0.5 9 0.5 2 Q0.5 0.5 2 0.5Z" fill="#3176b5"/></svg>843.555.0142</li>
          <li><svg class="contact__icon" viewBox="0 0 10 10"><rect x="0.7" y="2" width="8.6" height="6" fill="none" stroke="#3176b5" stroke-width="1"/><path d="M0.7 2 L5 5.5 L9.3 2" fill="none" stroke="#3176b5" stroke-width="1"/></svg>dwhitfield@velmora.org</li>
          <li><svg class="contact__icon" viewBox="0 0 10 10"><circle cx="5" cy="5" r="4.3" fill="none" stroke="#3176b5" stroke-width="1"/><ellipse cx="5" cy="5" rx="1.8" ry="4.3" fill="none" stroke="#3176b5" stroke-width="0.8"/><line x1="0.7" y1="5" x2="9.3" y2="5" stroke="#3176b5" stroke-width="0.8"/></svg>www.velmora.org</li>
        </ul>
      </div>
    </div>

    <p class="naics">NAICS: 5412-20/50/60, 5417-12/15/19, 5418-70<br>5612-20, 5614-11/21/40, 5615-20</p>
  </section>

  <section class="card card--back">
    <div class="card__backdrop" role="img" aria-label="Glowing blue circuit board traces on a starry deep-space background"></div>
    <div class="card__edge-line" style="top:48px;width:120px;"></div>
    <div class="card__edge-line" style="top:361px;left:46px;width:130px;"></div>

    <div class="brand brand--large"><span class="brand__square"></span>VELMORA</div>
    <div class="tagline tagline--large"><span class="tagline__rule"></span>BUILDING BETTER FUTURES</div>

    <svg class="badge" width="92" height="86" viewBox="0 0 92 86" role="img" aria-label="Certification badge">
      <circle cx="46" cy="40" r="36" fill="#3176b5" stroke="#e8c25a" stroke-width="4"/>
      <rect x="6" y="54" width="80" height="16" rx="3" fill="#e8c25a"/>
    </svg>
  </section>

</main>
</body>
</html>
```